Velora Entertainment

Logo for business card design

Target Market(s)

potential film investors and screenwriters

Industry/Entity Type

Business

Contact Information for Business Card

as shown, website here is a placeholder position

Requirements
Must have
• great visual appeal
Nice to have
• harmony of colors; must evoke spirit of
• U.S.-China cooperation

```html
<!DOCTYPE html>
<html lang="en">
<head>
<meta charset="utf-8">
<title>Velora Entertainment – Business Card</title>
<link href="https://fonts.googleapis.com/css2?family=Open+Sans:wght@400;600&display=swap" rel="stylesheet">
<style>
  :root {
    --backdrop: #3c3c3c;
    --card: #ffffff;
    --band: #979797;
    --ink: #141414;
    --ink-soft: #222222;
    --red: #e30613;
    --yellow: #ffdd00;
    --navy: #17177a;
  }
  html, body {
    margin: 0;
    padding: 0;
    width: 1105px;
    height: 1200px;
    overflow: hidden;
    background: var(--backdrop);
    font-family: "Open Sans", sans-serif;
  }
  .card {
    position: absolute;
    left: 52px;
    top: 314px;
    width: 1000px;
    height: 571px;
    background: var(--card);
    box-shadow: 0 4px 14px rgba(0,0,0,0.45);
    overflow: hidden;
  }
  .brand {
    position: absolute;
    left: 61px;
    top: 110px;
    display: flex;
    align-items: center;
    gap: 18px;
  }
  .brand-square {
    width: 62px;
    height: 62px;
    background: var(--red);
  }
  .brand-name {
    font-size: 40px;
    font-weight: 600;
    color: var(--ink);
    letter-spacing: 0.5px;
  }
  .name-band {
    position: absolute;
    left: 0;
    top: 278px;
    width: 100%;
    height: 113px;
    background: var(--band);
  }
  .person-name {
    position: absolute;
    left: 59px;
    top: 18px;
    margin: 0;
    font-size: 33px;
    font-weight: 600;
    color: var(--ink);
  }
  .person-title {
    position: absolute;
    left: 59px;
    top: 60px;
    margin: 0;
    font-size: 27px;
    font-weight: 400;
    color: var(--ink-soft);
  }
  .stripe {
    position: absolute;
    top: 0;
    height: 113px;
  }
  .stripe-red { left: 747px; width: 61px; background: var(--red); }
  .stripe-yellow { left: 811px; width: 63px; background: var(--yellow); }
  .stripe-navy { left: 877px; width: 61px; background: var(--navy); }
  .contact-list {
    position: absolute;
    left: 59px;
    top: 420px;
    margin: 0;
    padding: 0;
    list-style: none;
    font-size: 26px;
    color: var(--ink);
    line-height: 38px;
  }
  .contact-list li {
    display: flex;
    align-items: center;
    gap: 12px;
  }
  .contact-list svg {
    width: 25px;
    height: 25px;
    fill: var(--red);
    flex: none;
  }
  .address {
    position: absolute;
    right: 59px;
    top: 420px;
    margin: 0;
    text-align: right;
    font-style: normal;
    font-size: 26px;
    line-height: 38px;
    color: var(--ink);
  }
</style>
</head>
<body>
  <div class="card">
    <div class="brand">
      <div class="brand-square"></div>
      <div class="brand-name">Velora Entertainment</div>
    </div>

    <div class="name-band">
      <h1 class="person-name">Daniel Hart</h1>
      <p class="person-title">CEO/Founder</p>
      <div class="stripe stripe-red"></div>
      <div class="stripe stripe-yellow"></div>
      <div class="stripe stripe-navy"></div>
    </div>

    <ul class="contact-list">
      <li>
        <svg viewBox="0 0 24 24" aria-hidden="true"><path d="M6.6 10.8c1.4 2.8 3.8 5.1 6.6 6.6l2.2-2.2c.3-.3.7-.4 1-.2 1.1.4 2.3.6 3.6.6.6 0 1 .4 1 1V20c0 .6-.4 1-1 1C10.6 21 3 13.4 3 4c0-.6.4-1 1-1h3.5c.6 0 1 .4 1 1 0 1.2.2 2.4.6 3.6.1.3 0 .7-.2 1L6.6 10.8z"/></svg>
        555 210 4417
      </li>
      <li>
        <svg viewBox="0 0 24 24" aria-hidden="true"><path d="M7 1h10c1.1 0 2 .9 2 2v18c0 1.1-.9 2-2 2H7c-1.1 0-2-.9-2-2V3c0-1.1.9-2 2-2zm0 3v14h10V4H7zm5 15.2a1.2 1.2 0 100 2.4 1.2 1.2 0 000-2.4z"/></svg>
        555 382 0916
      </li>
      <li>
        <svg viewBox="0 0 24 24" aria-hidden="true"><path d="M2 5h20v14H2V5zm2 2v.4l8 5 8-5V7H4zm0 2.8V17h16V9.8l-8 5-8-5z"/></svg>
        hello@velora-ent.com
      </li>
    </ul>

    <address class="address">
      1420 Cedar Ridge Road<br>
      Portland, Oregon 97205<br>
      www.velora-ent.com
    </address>
  </div>
</body>
</html>
```